Hi Designers,

I will need 4 web pages designed. The web page looks like an App (if you click on the logo, or the icon on an iPad, it will take you to the website), but it is still a webpage.

Please check the attachment on this brief to understand what specific pages I need to be designed.

A .PSD (straight-up PhotoShop image) as final deliverable is fine, as long as you give us the exact “web color numbers”.

The design is for desktop and iPad but in a single unified web application, NOT separate web app and (native) iPad app.

Details:

Brightwater Policy Partners is developing a browser-based application for use on any mobile device or desktop. The app will be used by corporations to communicate with their employees regarding legal, regulatory and company requirements for conducting business. The app is known as “Harbor Guidance Portal.” When the user clicks on the icon for Harbor Guidance Portal, they will enter a site full of information that a company deems necessary for the employee to do his/her job. There are several content sections within the site, including a login page, training, policies, forms, news feeds and blogs.

The application has been built using Microsoft .NET, and fully supports CSS-type skinning; it uses traditional page layouts. We are seeking a product logo concept (image), a master application/desktop icon (image), as well as a full color scheme/theme/skin design for all areas of the application (header area, body text, menu bar, etc.) in the form of a CSS. The look should be clean, crisp and professional; nothing cartoony or whimsical. It should be easy to read and “airy”.

We have sketched prototypes for the basic application page layout that we can send as a next step of the process.
Updates

Screen shots have been uploaded to this project.  Please use them to guide your design.

Dear designers,

I apologize for the delay in providing feedback. My partners and I will provide feedback in a few days. Thank you for your patience.

Industry/Entity Type

Business

Font styles to use
Other font styles liked:
• see font on screen shots when uploaded

```html
<!DOCTYPE html>
<html lang="en">
<head>
<meta charset="utf-8">
<title>Harbor Guidance Portal</title>
<link href="https://fonts.googleapis.com/css2?family=Roboto:ital,wght@0,400;0,500;0,700;1,400&display=swap" rel="stylesheet">
<style>
  :root {
    --bg-top: #0f4f93;
    --bg-bottom: #0a2a55;
    --nav-top: #1e78d4;
    --nav-bottom: #0e56ad;
    --panel: #faf9f6;
    --divider: #e2e0db;
    --dark-top: #5a5a5a;
    --dark-bottom: #2f2f2f;
    --orange-top: #ef8a62;
    --orange-bottom: #c44a26;
    --link: #0a5fb8;
    --date: #0c5eb2;
    --text: #3a3a3a;
    --muted: #6d6d6d;
    --accent: #c4461f;
    --green: #8cc43f;
    --footer: #2470c8;
  }
  * { box-sizing: border-box; margin: 0; padding: 0; }
  html, body { width: 1200px; height: 985px; overflow: hidden; }
  body {
    font-family: "Roboto", Arial, sans-serif;
    background: radial-gradient(ellipse 900px 600px at 50% 20%, var(--bg-top), var(--bg-bottom));
    position: relative;
    color: var(--text);
  }
  .abs { position: absolute; }

  .brand { left: 0; width: 1200px; top: 44px; display: flex; justify-content: center; align-items: center; gap: 14px; }
  .brand-dot { width: 40px; height: 40px; border-radius: 50%; background: #ffffff; }
  .brand-name { color: #ffffff; font-size: 30px; font-weight: 400; letter-spacing: 0.5px; }

  .nav { left: 130px; top: 125px; width: 940px; height: 62px; background: linear-gradient(var(--nav-top), var(--nav-bottom)); border-radius: 2px; box-shadow: 0 2px 6px rgba(0,0,0,.3); }
  .nav-item { position: absolute; top: 10px; width: 90px; margin-left: -45px; text-align: center; color: #fff; font-size: 12px; }
  .nav-item svg { display: block; margin: 0 auto 6px; }
  .search { left: 571px; top: 141px; width: 242px; height: 30px; background: #fff; border-radius: 2px; font-size: 11px; font-style: italic; color: #777; padding: 9px 12px; }
  .search svg { position: absolute; right: 4px; top: 7px; }
  .badge { left: 858px; top: 118px; }
  .badge-count { left: 858px; top: 132px; width: 62px; text-align: center; color: #fff; font-size: 20px; font-weight: 500; }
  .user { left: 938px; top: 148px; color: #fff; font-size: 13px; display: flex; align-items: center; gap: 9px; }

  .panel { background: var(--panel); box-shadow: 0 2px 5px rgba(0,0,0,.35); }
  .panel-head { height: 44px; display: flex; align-items: center; padding-left: 14px; gap: 9px; color: #fff; font-size: 17px; }
  .panel-head.dark { background: linear-gradient(var(--dark-top), var(--dark-bottom)); }
  .panel-head.warm { background: linear-gradient(var(--orange-top), var(--orange-bottom)); }

  .news-item { height: 79px; border-bottom: 1px solid var(--divider); position: relative; }
  .news-item:last-child { border-bottom: none; }
  .date { position: absolute; left: 10px; top: 15px; width: 44px; height: 44px; background: var(--date); color: #fff; font-size: 13px; text-align: center; line-height: 17px; padding-top: 5px; }
  .news-title { position: absolute; left: 66px; top: 12px; width: 140px; color: var(--link); font-size: 13px; line-height: 17px; }
  .read-more { position: absolute; left: 66px; top: 51px; font-size: 12px; font-style: italic; color: var(--muted); }

  .photo { background: linear-gradient(135deg, #b88e6a, #6e7e96 55%, #2b3d5c); }
  .doc-title { margin: 12px 12px 4px; font-size: 13px; font-weight: 500; color: var(--link); }
  .doc-text { margin: 0 12px; font-size: 12px; font-style: italic; line-height: 20px; color: #555; }

  .blog-title { margin: 14px 13px 6px; font-size: 18px; font-weight: 500; color: var(--link); }
  .blog-text { margin: 0 13px; font-size: 13px; line-height: 23px; color: var(--text); }
  .blog-meta { margin: 14px 13px 0; font-size: 13px; color: var(--accent); }

  .list { list-style: none; padding: 14px 0 0 16px; }
  .list li { font-size: 13px; height: 25px; line-height: 18px; padding-left: 19px; position: relative; }
  .list li::before { content: ""; position: absolute; left: 0; top: 5px; width: 9px; height: 9px; border-radius: 50%; background: var(--date); }

  .report { height: 79px; border-bottom: 1px solid var(--divider); position: relative; }
  .report:last-child { border-bottom: none; }
  .thumb { position: absolute; left: 8px; top: 13px; width: 48px; height: 48px; border: 2px solid #d6d6d6; border-radius: 3px; }
  .report-title { position: absolute; left: 66px; top: 13px; font-size: 13px; color: var(--link); }
  .report-text { position: absolute; left: 66px; top: 33px; width: 140px; font-size: 12px; line-height: 18px; color: var(--text); }

  .faq { border-bottom: 1px solid var(--divider); padding: 11px 12px 10px 19px; height: 89px; }
  .faq:last-child { border-bottom: none; }
  .faq-q { font-size: 13px; line-height: 17px; color: var(--link); }
  .faq-a { font-size: 12px; line-height: 17px; color: var(--text); margin-top: 1px; }

  .footer-line { left: 130px; top: 884px; width: 940px; height: 10px; background: radial-gradient(ellipse at 50% 0%, rgba(0,0,0,.45), transparent 70%); }
  .footer { left: 0; width: 1200px; top: 924px; text-align: center; font-size: 13px; line-height: 21px; color: var(--footer); }
</style>
</head>
<body>
  <header class="abs brand">
    <span class="brand-dot"></span>
    <span class="brand-name">Harbor Guidance Portal</span>
  </header>

  <nav class="abs nav">
    <div class="nav-item" style="left:48px">
      <svg width="22" height="20" viewBox="0 0 22 20"><path d="M11 1 1 10h3v9h5v-6h4v6h5v-9h3z" fill="#fff"/></svg>HOME</div>
    <div class="nav-item" style="left:144px">
      <svg width="30" height="20" viewBox="0 0 30 20"><g fill="#fff"><rect x="0" y="1" width="4" height="3"/><rect x="6" y="1" width="24" height="3"/><rect x="0" y="6" width="4" height="3"/><rect x="6" y="6" width="24" height="3"/><rect x="0" y="11" width="4" height="3"/><rect x="6" y="11" width="24" height="3"/><rect x="0" y="16" width="4" height="3"/><rect x="6" y="16" width="24" height="3"/></g></svg>MENU</div>
    <div class="nav-item" style="left:246px">
      <svg width="34" height="20" viewBox="0 0 34 20"><path d="M8 2h18c4 0 6 4 7 9s0 9-3 9-5-5-7-5H11c-2 0-4 5-7 5S0 16 1 11 4 2 8 2z" fill="#fff"/><g fill="#1565be"><rect x="7" y="7" width="2" height="6"/><rect x="5" y="9" width="6" height="2"/><circle cx="25" cy="8" r="1.5"/><circle cx="28" cy="11" r="1.5"/></g></svg>GAME</div>
    <div class="nav-item" style="left:341px">
      <svg width="22" height="20" viewBox="0 0 22 20"><g fill="#fff"><rect x="1" y="0" width="5" height="20"/><rect x="8" y="4" width="5" height="16"/><rect x="15" y="9" width="5" height="11"/></g></svg>HCP 360</div>
  </nav>

  <div class="abs search">Search...
    <svg width="18" height="16" viewBox="0 0 18 16"><circle cx="6" cy="6" r="4.5" fill="none" stroke="#333" stroke-width="2"/><path d="M9.5 9.5 16 14" stroke="#5a3d8a" stroke-width="3" stroke-linecap="round"/></svg>
  </div>

  <svg class="abs badge" width="62" height="63" viewBox="0 0 62 63"><path d="M0 0h62v44L31 63 0 44z" fill="var(--green)"/></svg>
  <div class="abs badge-count">475</div>

  <div class="abs user">
    <svg width="19" height="18" viewBox="0 0 19 18"><circle cx="9.5" cy="5" r="4.5" fill="#fff"/><path d="M0 18c0-6 4-8 9.5-8S19 12 19 18z" fill="#fff"/></svg>
    <span>Dana Hollis</span>
    <svg width="12" height="7" viewBox="0 0 12 7" style="margin-left:4px"><path d="M0 0h12L6 7z" fill="#fff"/></svg>
  </div>

  <!-- Left column -->
  <section class="abs panel" style="left:130px;top:205px;width:221px;height:279px">
    <div class="panel-head dark">
      <svg width="24" height="18" viewBox="0 0 24 18"><path d="M2 7h5l11-6v16L7 11H2z" fill="#e04a3a"/><rect x="4" y="11" width="4" height="6" fill="#ddd"/></svg>
      Compliance News</div>
    <div class="news-item"><div class="date">Nov<br>18</div><div class="news-title">Sed ut perspiciatis unde omnis</div><div class="read-more">Read More</div></div>
    <div class="news-item"><div class="date">Nov<br>18</div><div class="news-title">Sed ut perspiciatis unde omnis</div><div class="read-more">Read More</div></div>
    <div class="news-item"><div class="date">Nov<br>18</div><div class="news-title">Sed ut perspiciatis unde omnis</div><div class="read-more">Read More</div></div>
  </section>

  <section class="abs panel" style="left:130px;top:495px;width:221px;height:319px">
    <div class="panel-head dark" style="padding-left:12px;gap:6px">
      <svg width="18" height="16" viewBox="0 0 18 16"><rect x="1" y="1" width="16" height="4" fill="#4a8ad0"/><rect x="1" y="6" width="16" height="4" fill="#e0a030"/><rect x="1" y="11" width="16" height="4" fill="#5aa84a"/></svg>
      Document Library</div>
    <div class="photo" role="img" aria-label="Photo of people studying at tables in a library" style="margin:12px 12px 0;width:197px;height:134px"></div>
    <div class="doc-title">Sed ut perspiciatis unde omnis</div>
    <div class="doc-text">Lorem ipsum dolor sit amet, con-sectetur adipisicing eitseo eiusmod tempor incididunt ut labore et dolore magna aliqua.</div>
  </section>

  <!-- Center column -->
  <section class="abs panel" style="left:360px;top:205px;width:480px;height:369px">
    <div class="panel-head warm">
      <svg width="24" height="20" viewBox="0 0 24 20"><ellipse cx="11" cy="9" rx="10" ry="8" fill="#4fb3e8"/><path d="M5 15l-2 5 6-3z" fill="#4fb3e8"/><rect x="5" y="7" width="12" height="2" fill="#fff"/><rect x="5" y="11" width="9" height="2" fill="#fff"/></svg>
      Compliance Blog</div>
    <div class="photo" role="img" aria-label="Photo of a hand touching a glowing digital interface" style="margin:9px 11px 0;width:458px;height:161px;border:2px solid #c9ccd2;background:radial-gradient(circle at 50% 40%, #dde7f2, #5d7290 35%, #26344c 85%)"></div>
    <div class="blog-title">Sed ut perspiciatis unde omnis</div>
    <div class="blog-text">Lorem ipsum dolor sit amet,&nbsp; consectetur adipisicing eitseo eiusmod tempor incididunt ut labore et dolore magna aliqua.Sed ut perspiciatis unde omnis iste natus error sit voluptatem accusantium...</div>
    <div class="blog-meta">Read More&nbsp; |&nbsp; Posted on 2 days...</div>
  </section>

  <section class="abs panel" style="left:360px;top:588px;width:235px;height:226px">
    <div class="panel-head warm">
      <svg width="24" height="22" viewBox="0 0 24 22"><g fill="none" stroke="#c8d448" stroke-width="3"><rect x="2" y="10" width="11" height="6" rx="3" transform="rotate(-40 7 13)"/><rect x="11" y="5" width="11" height="6" rx="3" transform="rotate(-40 16 8)"/></g></svg>
      Relevant Links</div>
    <ul class="list">
      <li>Sed ut perspiciatis unde</li><li>Duis aute irure dolor</li><li>dolore magna aliqua</li>
      <li>Sed ut perspiciatis unde</li><li>Duis aute irure dolor</li><li>dolore magna aliqua</li>
    </ul>
  </section>

  <section class="abs panel" style="left:606px;top:588px;width:235px;height:226px">
    <div class="panel-head warm">
      <svg width="20" height="22" viewBox="0 0 20 22"><path d="M2 1h11l5 5v15H2z" fill="#fff"/><g fill="#4a8ad0"><rect x="5" y="8" width="10" height="2"/><rect x="5" y="12" width="10" height="2"/><rect x="5" y="16" width="7" height="2"/></g></svg>
      Forms</div>
    <ul class="list">
      <li>Sed ut perspiciatis unde</li><li>Duis aute irure dolor</li><li>dolore magna aliqua</li>
      <li>Sed ut perspiciatis unde</li><li>Duis aute irure dolor</li><li>dolore magna aliqua</li>
    </ul>
  </section>

  <!-- Right column -->
  <section class="abs panel" style="left:850px;top:205px;width:221px;height:279px">
    <div class="panel-head dark" style="padding-left:10px;gap:7px">
      <svg width="22" height="22" viewBox="0 0 22 22"><rect x="1" y="8" width="5" height="13" fill="#e05a3a"/><rect x="8" y="2" width="5" height="19" fill="#4fb3e8"/><rect x="15" y="11" width="5" height="10" fill="#8cc43f"/></svg>
      Reports</div>
    <div class="report"><div class="thumb" role="img" aria-label="Spreadsheet report thumbnail" style="background:linear-gradient(#dfe8f4,#f4f6f9)"></div><div class="report-title">Perspiciatis unde</div><div class="report-text">Eiusmod tempor incidi-dunt ut labore..</div></div>
    <div class="report"><div class="thumb" role="img" aria-label="Pie and bar chart report thumbnail" style="background:linear-gradient(135deg,#f6f6f6,#e6eef0)"></div><div class="report-title">Perspiciatis unde</div><div class="report-text">Eiusmod tempor incidi-dunt ut labore..</div></div>
    <div class="report" style="height:77px"><div class="thumb" role="img" aria-label="Chart report thumbnail" style="top:11px;background:linear-gradient(135deg,#f2f2f2,#e8d8e6)"></div><div class="report-title" style="top:11px">Perspiciatis unde</div><div class="report-text" style="top:31px">Eiusmod tempor incidi-dunt ut labore..</div></div>
  </section>

  <section class="abs panel" style="left:850px;top:495px;width:221px;height:319px">
    <div class="panel-head dark">
      <svg width="30" height="20" viewBox="0 0 30 20"><ellipse cx="11" cy="9" rx="10" ry="7" fill="#f2c21a"/><ellipse cx="19" cy="11" rx="10" ry="7" fill="#f7d445"/></svg>
      FAQ’s</div>
    <div class="faq"><div class="faq-q">Sed ut perspiciatis unde omnis?</div><div class="faq-a">Veritatis et quasi architecto beatae vitae dicta sunt...</div></div>
    <div class="faq"><div class="faq-q">Sed ut perspiciatis unde omnis?</div><div class="faq-a">Veritatis et quasi architecto beatae vitae dicta sunt...</div></div>
    <div class="faq"><div class="faq-q">Sed ut perspiciatis unde omnis?</div><div class="faq-a">Veritatis et quasi architecto beatae vitae dicta sunt...</div></div>
  </section>

  <div class="abs footer-line"></div>
  <footer class="abs footer">Copyright © 2013. Harbor Guidance Portal<br>All Right Reserved</footer>
</body>
</html>
```